Website Design for Wheels for Servicemen.org - Donated Cars to Disabled Vets

Need a Wordpress website. The coding now, esp. the CDONT coding is not supported by many hosting sites. Looking for a landing page to generate leads.

Logo Text

look at current one for ideas

Coding

Coded - Design and coding required

Number of Pages Required

1 page

Requirements
Must have
• look at current website at www.wheelsforservicemen.org
Nice to have
• look at this site: http://givevehicletoservicemen.org

```html
<!DOCTYPE html>
<html lang="en">
<head>
<meta charset="utf-8">
<title>Wheels for Servicemen – Donate Your Car</title>
<link href="https://fonts.googleapis.com/css2?family=Montserrat:wght@400;600;700&family=Open+Sans:ital,wght@0,400;0,600;0,700;1,400&family=Oswald:wght@500&display=swap" rel="stylesheet">
<style>
:root{
  --blue:#1d5ea6;
  --blue-dark:#0f3d73;
  --navy:#0d1b2e;
  --red:#b4122e;
  --red-dark:#8f0c22;
  --ink:#333333;
  --muted:#777777;
  --line:#dddddd;
  --light:#eeeeee;
  --white:#ffffff;
}
*{box-sizing:border-box;margin:0;padding:0}
html,body{width:1200px;height:2514px;overflow:hidden;background:var(--white)}
body{font-family:"Open Sans",Arial,sans-serif;color:var(--ink);position:relative}
.abs{position:absolute}
h1,h2,h3,h4,.mont{font-family:"Montserrat",Arial,sans-serif}

/* top bar */
.topbar{left:0;top:0;width:1200px;height:30px;background:var(--blue);color:var(--white);font-size:11px}
.topbar .info{position:absolute;top:8px;display:flex;align-items:center;gap:7px;white-space:nowrap}
.topbar .donate{position:absolute;right:100px;top:0;width:170px;height:30px;background:var(--red);font-family:Montserrat,sans-serif;font-weight:700;font-size:12px;display:flex;align-items:center;justify-content:center}

/* header */
.header{left:0;top:30px;width:1200px;height:94px;background:var(--white)}
.brand{left:100px;top:28px;display:flex;align-items:center;gap:12px}
.brand-mark{width:34px;height:34px;background:var(--red);border-radius:4px}
.brand-name{font-family:Montserrat,sans-serif;font-weight:600;font-size:20px;color:var(--blue)}
.nav{right:100px;top:40px;display:flex;gap:63px;font-size:12px;color:#444}

/* hero */
.hero{left:0;top:124px;width:1200px;height:548px;background:linear-gradient(100deg,#1a2a40 0%,#0d1b2e 55%,#0a1422 100%)}
.hero-photo{left:0;top:0;width:680px;height:548px;background:radial-gradient(ellipse at 40% 40%,#3a4c66 0%,#1b2b42 60%,transparent 100%)}
.hero-caption{left:315px;top:370px;color:var(--white)}
.hero-caption h1{font-family:"Open Sans",sans-serif;font-weight:400;font-size:30px}
.hero-caption p{font-size:18px;margin-top:10px}
.dots{left:578px;top:472px;display:flex;gap:6px}
.dots i{width:7px;height:7px;border-radius:50%;background:#8090a6}
.dots i:first-child{background:var(--blue)}
.form-card{left:680px;top:50px;width:421px;height:418px;background:var(--white);border-radius:6px;padding:26px 30px}
.form-card .lead{font-size:17px;color:#444;line-height:26px}
.form-card .phone{font-family:Montserrat,sans-serif;font-weight:700;font-size:26px;color:var(--red)}
.form-card h2{font-size:24px;color:var(--blue);margin-top:4px}
.fields{display:grid;grid-template-columns:1fr 1fr;gap:11px 12px;margin-top:18px}
.fields div{height:36px;border:1px solid #ccc;border-radius:3px;font-size:11px;color:#888;padding:10px 14px}
.form-card .submit{margin-top:16px;height:52px;background:linear-gradient(var(--red),var(--red-dark));color:var(--white);border-radius:3px;font-family:Montserrat,sans-serif;font-weight:700;font-size:16px;display:flex;align-items:center;justify-content:center}

/* service cards */
.services{left:100px;top:625px;width:1001px;height:230px;background:var(--white);border-radius:6px;box-shadow:0 2px 10px rgba(0,0,0,.12)}
.svc{top:22px;width:306px;height:196px;border-radius:5px;overflow:hidden}
.svc .bar{position:absolute;left:0;bottom:0;width:100%;height:46px;background:rgba(0,0,0,.65);color:var(--white);font-family:Montserrat,sans-serif;font-weight:700;font-size:16px;padding:13px 16px;display:flex;gap:9px;align-items:center}

/* how it works */
.section-title{left:0;width:1200px;text-align:center;font-family:Montserrat,sans-serif;font-weight:700;font-size:25px;color:#333}
.section-sub{left:0;width:1200px;text-align:center;font-size:14px;color:var(--muted)}
.step{top:1012px;width:330px;display:flex;gap:14px}
.step .num{font-family:Oswald,"Arial Narrow",sans-serif;font-weight:500;font-size:60px;color:#c7c7c7;line-height:60px}
.step h4{font-size:13px;font-weight:700;margin-top:6px;color:#222}
.step p{font-size:12px;color:var(--muted);line-height:22px;margin-top:4px}
.divider{left:150px;top:1126px;width:900px;height:10px;border-radius:50%;box-shadow:0 8px 12px -6px rgba(0,0,0,.2)}

/* why */
.why{top:1268px;width:315px;height:113px;border:1px solid var(--line);border-radius:3px;padding:26px 28px;font-size:13px;line-height:23px;color:var(--muted)}
.why b{color:var(--blue);font-weight:600}

/* about */
.about{left:0;top:1456px;width:1200px;height:357px;background:linear-gradient(90deg,#2d6fb3,#3a82c4 50%,#2d6fb3)}
.about h2{position:absolute;top:92px;width:1200px;text-align:center;color:var(--white);font-size:25px}
.about p{position:absolute;top:140px;left:220px;width:760px;text-align:center;color:var(--white);font-size:15px;line-height:31px}
.about .btn{position:absolute;left:518px;top:218px;width:164px;height:46px;background:var(--red);color:var(--white);font-family:Montserrat,sans-serif;font-weight:700;font-size:14px;display:flex;align-items:center;justify-content:center;border-radius:2px}

/* donate today / testimonials */
.col-title{top:1885px;font-family:Montserrat,sans-serif;font-weight:700;font-size:24px;color:#333}
.photo-frame{left:100px;top:1951px;width:246px;height:170px;border:5px solid #e4e4e4}
.checks{left:378px;top:1960px;list-style:none;font-size:13px;color:#333}
.checks li{display:flex;gap:10px;align-items:center;height:29px}
.avatar{left:678px;top:1952px;width:148px;height:148px;border-radius:50%;border:5px solid #e8e8e8;background:linear-gradient(#c9b8a6,#8d98a8)}
.quote{left:852px;top:1956px;width:250px}
.quote h4{font-size:15px;color:#333;font-weight:600}
.quote .role{font-size:12px;color:var(--muted);margin-top:4px}
.quote p{font-style:italic;font-size:12px;line-height:23px;color:#555;margin-top:12px}
.arrows{left:1074px;top:1960px;color:#aaa;font-size:14px;letter-spacing:6px}

/* footer */
.footer{left:0;top:2190px;width:1200px;height:265px;background:var(--light)}
.f-title{top:44px;font-family:Montserrat,sans-serif;font-weight:700;font-size:14px;color:#333}
.f-text{font-size:11px;color:#666;line-height:22px}
.email-in{left:100px;top:105px;width:315px;height:36px;background:var(--white);border:1px solid #ccc;border-radius:3px;font-size:11px;color:#777;padding:11px 14px}
.subscribe{left:100px;top:160px;width:136px;height:40px;background:var(--red);color:var(--white);font-family:Montserrat,sans-serif;font-weight:700;font-size:13px;display:flex;align-items:center;justify-content:center;border-radius:3px}
.socials{left:916px;top:103px;display:flex;gap:10px}
.socials i{width:28px;height:28px;border-radius:50%;background:var(--red-dark)}
.badges{left:916px;top:152px;width:185px;height:60px;background:var(--white);border:1px solid #ddd;display:flex;gap:22px;align-items:center;padding:0 18px}
.copy{left:0;top:2455px;width:1200px;height:59px;display:flex;justify-content:center;align-items:center;gap:20px;font-size:11px;color:#555}
</style>
</head>
<body>

<div class="abs topbar">
  <span class="info" style="left:100px">
    <svg width="13" height="10" viewBox="0 0 13 10"><rect x="0.5" y="0.5" width="12" height="9" fill="none" stroke="#fff"/><path d="M0.5 0.5 L6.5 5.5 L12.5 0.5" fill="none" stroke="#fff"/></svg>
    info@wheelsforservicemen.org</span>
  <span class="info" style="left:326px">
    <svg width="9" height="12" viewBox="0 0 9 12"><path d="M4.5 12 C1 7 0 5.5 0 4.5 A4.5 4.5 0 0 1 9 4.5 C9 5.5 8 7 4.5 12Z" fill="#fff"/><circle cx="4.5" cy="4.5" r="1.6" fill="#1d5ea6"/></svg>
    120 Street name, City name, Country name : 65236565</span>
  <span class="info" style="left:710px">
    <svg width="13" height="12" viewBox="0 0 13 12"><path d="M1.5 8 V6 A5 5 0 0 1 11.5 6 V8" fill="none" stroke="#fff" stroke-width="1.5"/><rect x="0.5" y="7" width="3" height="4" fill="#fff"/><rect x="9.5" y="7" width="3" height="4" fill="#fff"/></svg>
    Call Us : 1-800-555-0142</span>
  <div class="donate">DONATE YOUR CAR</div>
</div>

<header class="abs header">
  <div class="abs brand"><div class="brand-mark"></div><div class="brand-name">Wheels for Servicemen</div></div>
  <nav class="abs nav"><span>ABOUT US</span><span>SERVICES</span><span>WE TOW IT</span><span>TAX WRITE-OFF</span><span>CONTACT US</span></nav>
</header>

<section class="abs hero">
  <div class="abs hero-photo" role="img" aria-label="Man in a dark suit cupping a small white toy car in his hands"></div>
  <div class="abs hero-caption"><h1>Donate Your Car :</h1><p>Full Tax Deduction - Running or Not</p></div>
  <div class="abs dots"><i></i><i></i><i></i><i></i></div>
  <div class="abs form-card">
    <div class="lead">LEASE FILL OUT FORM OR CALL</div>
    <div class="lead">TOLL-FREE <span class="phone">1-800-555-0142</span></div>
    <h2>DONATE HERE</h2>
    <div class="fields">
      <div>Name</div><div>Email</div>
      <div>Phone Number</div><div>Cell Phone</div>
      <div>Address</div><div>City</div>
      <div>State</div><div>Zip Code</div>
    </div>
    <div class="submit">CLICK HERE FOR DONATE HERE</div>
  </div>
</section>

<section class="abs services">
  <div class="abs svc" style="left:19px;background:linear-gradient(#eef2f5,#c9d3dc)" role="img" aria-label="Smiling call center agent wearing a headset">
    <div class="bar">CALL US <svg width="13" height="13" viewBox="0 0 13 13"><circle cx="6.5" cy="6.5" r="6" fill="#f2a81d"/><path d="M5 3.5 L8 6.5 L5 9.5" fill="none" stroke="#222" stroke-width="1.6"/></svg></div>
  </div>
  <div class="abs svc" style="left:347px;background:linear-gradient(#6a7282,#2c3240)" role="img" aria-label="Row of parked cars">
    <div class="bar">WE TOW IT <svg width="13" height="13" viewBox="0 0 13 13"><circle cx="6.5" cy="6.5" r="6" fill="#f2a81d"/><path d="M5 3.5 L8 6.5 L5 9.5" fill="none" stroke="#222" stroke-width="1.6"/></svg></div>
  </div>
  <div class="abs svc" style="left:675px;background:linear-gradient(135deg,#f7e8c8,#e0a35a)" role="img" aria-label="Toy car with a calculator and notebook">
    <div class="bar">TAX WRITE - OFF <svg width="13" height="13" viewBox="0 0 13 13"><circle cx="6.5" cy="6.5" r="6" fill="#f2a81d"/><path d="M5 3.5 L8 6.5 L5 9.5" fill="none" stroke="#222" stroke-width="1.6"/></svg></div>
  </div>
</section>

<h2 class="abs section-title" style="top:903px">HOW IT WORKS</h2>
<p class="abs section-sub" style="top:952px">We only work with quality charities that truly care about their cause and use your contributions most effectively.</p>
<div class="abs step" style="left:110px"><div class="num">01</div><div><h4>FILL OUT THE SIMPLE FORM</h4><p>Use our online vehicle donation form to submit your information.</p></div></div>
<div class="abs step" style="left:453px"><div class="num">02</div><div><h4>SCHEDULE YOUR FREE PICK-UP</h4><p>Use our online vehicle donation form to submit your information.</p></div></div>
<div class="abs step" style="left:800px"><div class="num">03</div><div><h4>RECEIVE TAX DEDUCTION</h4><p>Use our online vehicle donation form to submit your information.</p></div></div>
<div class="abs divider"></div>

<h2 class="abs section-title" style="top:1190px">WHY DONATE YOUR CAR TO US?</h2>
<div class="abs why" style="left:100px"><b>IRS 501(c)3 Approved:</b> Free 24/7 Pickup with No DMV Hassles.</div>
<div class="abs why" style="left:443px"><b>Free Local Towing to You:</b> We will pick up your car donation, running or not, when it's most convenient, at home or work.</div>
<div class="abs why" style="left:786px"><b>All Cars Accepted :</b> We take your car regardless of its condition or registration status...</div>

<section class="abs about" role="img" aria-label="Blue-tinted hand holding out a car key">
  <h2>ABOUT WHEELS FOR SERVICEMEN</h2>
  <p>es simplemente el texto de relleno de las imprentas y archivos de texto. Lorem Ipsum ha sido el texto de relleno estándar de las industrias desde el año 1500</p>
  <div class="btn">READ MORE INFO</div>
</section>

<h2 class="abs col-title" style="left:100px">DONATE YOUR CAR TODAY!</h2>
<div class="abs photo-frame" style="background:linear-gradient(#8a9a7a,#6b5a44)" role="img" aria-label="Vehicle on a muddy road with soldiers beside it"></div>
<ul class="abs checks">
  <li><svg width="12" height="10" viewBox="0 0 12 10"><path d="M1 5 L4.5 8.5 L11 1" fill="none" stroke="#f2a81d" stroke-width="2"/></svg>You have no costs.</li>
  <li><svg width="12" height="10" viewBox="0 0 12 10"><path d="M1 5 L4.5 8.5 L11 1" fill="none" stroke="#f2a81d" stroke-width="2"/></svg>Free towing, running or not.</li>
  <li><svg width="12" height="10" viewBox="0 0 12 10"><path d="M1 5 L4.5 8.5 L11 1" fill="none" stroke="#f2a81d" stroke-width="2"/></svg>We issue you an IRS tax receipt.</li>
  <li><svg width="12" height="10" viewBox="0 0 12 10"><path d="M1 5 L4.5 8.5 L11 1" fill="none" stroke="#f2a81d" stroke-width="2"/></svg>We take care of all paperwork.</li>
  <li><svg width="12" height="10" viewBox="0 0 12 10"><path d="M1 5 L4.5 8.5 L11 1" fill="none" stroke="#f2a81d" stroke-width="2"/></svg>And we take care of DMV &amp; Smog issues.</li>
</ul>

<h2 class="abs col-title" style="left:676px">WHAT OUR CLIENT’S SAY</h2>
<div class="abs avatar" role="img" aria-label="Portrait of the client"></div>
<div class="abs arrows">‹ ›</div>
<div class="abs quote">
  <h4>Marcus Hale</h4>
  <div class="role">Business man</div>
  <p>Lorem Ipsum is simply dummy text of the printing and typesetting industry. Lorem Ipsum has been the industry's standard dummy text ever since the 1500s</p>
</div>

<footer class="abs footer">
  <h4 class="abs f-title" style="left:102px">NEWSLETTER SIGNUP</h4>
  <div class="abs f-text" style="left:102px;top:70px">Get our recent updates through your email id</div>
  <div class="abs email-in">Enter your email id</div>
  <div class="abs subscribe">SUBSCRIBE</div>

  <h4 class="abs f-title" style="left:489px">WELCOME</h4>
  <div class="abs f-text" style="left:489px;top:72px">Home<br>About Us<br>Services<br>We tow it<br>Tax write-Off<br>Contact Us</div>

  <h4 class="abs f-title" style="left:667px">CONTACT INFO</h4>
  <div class="abs f-text" style="left:667px;top:72px"><span style="color:var(--blue);font-weight:600;font-size:12px">Wheels for Servicemen</span><br>120 Street name, City name,<br>Country name : 65236565</div>
  <div class="abs f-text" style="left:667px;top:150px;display:flex;gap:10px;align-items:center"><svg width="11" height="11" viewBox="0 0 11 11"><path d="M2 0 L4 3 L3 4.5 Q4.5 7 6.5 8 L8 7 L11 9 L9.5 11 Q3 10 0 2Z" fill="#b4122e"/></svg>1-800-555-0142</div>
  <div class="abs f-text" style="left:667px;top:174px;display:flex;gap:10px;align-items:center"><svg width="12" height="9" viewBox="0 0 12 9"><rect x="0.5" y="0.5" width="11" height="8" fill="none" stroke="#b4122e"/><path d="M0.5 0.5 L6 5 L11.5 0.5" fill="none" stroke="#b4122e"/></svg>info@wheelsforservicemen.org</div>

  <h4 class="abs f-title" style="left:916px">FOLLOW US</h4>
  <div class="abs f-text" style="left:916px;top:70px">Connect with our social network</div>
  <div class="abs socials"><i></i><i></i><i></i><i></i></div>
  <div class="abs badges">
    <div style="width:44px;height:44px;border-radius:50%;background:#c8d4e0"></div>
    <div style="width:86px;height:30px;background:#d8d8d8;border-radius:3px"></div>
  </div>
</footer>

<div class="abs copy"><span>© 2016. Wheels for Servicemen. All rights reserved.</span><span>Terms &amp; Conditions</span><span>/</span><span>Privacy Policy</span><span>/</span><span>Disclaimer</span></div>

</body>
</html>
```